New Funeral Home brochure deign

We need a full color company brochure that can communicate our company values and services to families we serve. A draft is attached.

Industry/Entity Type

Funeral Home

Requirements
Must have
• We need a full color company brochure that can communicate our company values and services to families we serve. A draft is attached.

```html
<!DOCTYPE html>
<html lang="en">
<head>
<meta charset="utf-8">
<title>Halloway's Funeral Service Brochure</title>
<link href="https://fonts.googleapis.com/css2?family=Jost:ital,wght@0,300;0,400;1,300&family=Tinos&family=Playball&display=swap" rel="stylesheet">
<style>
  :root {
    --backdrop: #2b2b2d;
    --paper-light: #f0c36e;
    --paper-mid: #e2a847;
    --paper-dark: #b8781f;
    --frame-line: rgba(255, 246, 225, 0.85);
    --ink: #2c2620;
    --card-white: #f3eee4;
    --card-aged: #e4dccd;
    --card-grey: #55514c;
  }
  * { box-sizing: border-box; margin: 0; padding: 0; }
  html, body { width: 960px; height: 1200px; overflow: hidden; background: var(--backdrop); }
  .canvas { position: relative; width: 960px; height: 1200px; }

  .spread {
    position: absolute; left: 58px; width: 845px; height: 326px;
    background: radial-gradient(ellipse at 50% 45%, var(--paper-light) 0%, var(--paper-mid) 55%, var(--paper-dark) 100%);
    box-shadow: 0 6px 18px rgba(0,0,0,0.55);
  }
  .spread--hospice { top: 58px; }
  .spread--veterans { top: 445px; }
  .spread--facility { top: 831px; }

  .panel-frame {
    position: absolute; top: 12px; width: 398px; height: 302px;
    border: 1px solid var(--frame-line);
  }
  .panel-frame--left { left: 12px; }
  .panel-frame--right { left: 434px; }

  /* vintage photo stack with deckled edges */
  .photo-stack {
    position: absolute; width: 306px; height: 194px;
    filter: drop-shadow(0 3px 5px rgba(0,0,0,0.45));
  }
  .photo-stack--left { left: 60px; top: 62px; }
  .photo-stack--right { left: 476px; top: 62px; width: 302px; }
  .deckled {
    --r: 2.5px;
    position: absolute; inset: 0; padding: var(--r);
    -webkit-mask:
      radial-gradient(var(--r) at var(--r) var(--r), #000 97%, #0000) round calc(-1 * var(--r)) calc(-1 * var(--r)) / calc(2 * var(--r)) calc(2 * var(--r)),
      linear-gradient(#000 0 0) content-box;
    mask:
      radial-gradient(var(--r) at var(--r) var(--r), #000 97%, #0000) round calc(-1 * var(--r)) calc(-1 * var(--r)) / calc(2 * var(--r)) calc(2 * var(--r)),
      linear-gradient(#000 0 0) content-box;
  }
  .back-card--grey { background: linear-gradient(180deg, var(--card-grey), #8a857d 30%, var(--card-aged) 60%); transform: rotate(-3deg) translate(4px, -6px); }
  .back-card--aged { background: var(--card-aged); transform: rotate(2.5deg) translate(2px, 8px); }
  .back-card--pale { background: #ece6da; transform: rotate(-1.5deg) translate(-6px, 2px); }
  .front-card { background: var(--card-white); }
  .front-card .photo { position: absolute; inset: 7px 10px 9px 10px; }

  .photo--hospice { background: linear-gradient(135deg, #e9a3a3 0%, #f2c1b6 50%, #f6e8e2 100%); }
  .photo--flag { background: linear-gradient(160deg, #5d6a4a 0%, #3b3f8c 45%, #d8d6dc 75%, #7a8c5e 100%); }
  .photo--guard { background: linear-gradient(135deg, #c8d2dc 0%, #1e1f22 40%, #6b3b22 75%, #e8e6e3 100%); }

  .collage { display: grid; grid-template-columns: 54% 1fr; grid-template-rows: 57% 1fr; gap: 4px 3px; background: var(--card-white); }
  .collage__exterior { background: linear-gradient(180deg, #a9c6e0 0%, #d6c5a7 45%, #c7b391 70%, #2f4a7a 100%); }
  .collage__lounge { background: linear-gradient(135deg, #9a8e7d 0%, #cfc7bb 50%, #6e6253 100%); }
  .collage__foyer { grid-row: 1 / 3; grid-column: 2; background: linear-gradient(180deg, #efe9df 0%, #d9cfbf 45%, #5a4f45 80%, #3c342d 100%); }

  .panel-copy {
    position: absolute; left: 434px; top: 12px; width: 398px; height: 302px;
    text-align: center; color: var(--ink);
  }
  .headline {
    margin-top: 52px; font-family: "Tinos", "Times New Roman", serif;
    font-weight: 400; line-height: 1.05;
  }
  .headline__main { display: block; font-size: 25px; letter-spacing: 0.3px; }
  .headline__link { display: block; font-size: 16px; margin-top: 6px; }
  .headline__script {
    display: block; font-family: "Playball", cursive; font-size: 34px;
    margin-top: 4px; line-height: 1.15;
  }
  .body-copy {
    width: 300px; margin: 24px auto 0; font-family: "Jost", sans-serif;
    font-weight: 300; font-size: 8.3px; line-height: 1.4;
  }
  .body-copy--closing { margin-top: 13px; font-style: italic; }
</style>
</head>
<body>
<main class="canvas">

  <section class="spread spread--hospice">
    <div class="panel-frame panel-frame--left"></div>
    <div class="panel-frame panel-frame--right"></div>
    <div class="photo-stack photo-stack--left">
      <div class="deckled back-card--grey"></div>
      <div class="deckled back-card--aged"></div>
      <div class="deckled back-card--pale"></div>
      <div class="deckled front-card"><div class="photo photo--hospice" role="img" aria-label="Close-up of a caring hand resting on an elderly woman's arm in a pink sweater"></div></div>
    </div>
    <div class="panel-copy">
      <h2 class="headline">
        <span class="headline__main">ENDURING RELATIONSHIPS</span>
        <span class="headline__link">WITH</span>
        <span class="headline__script">Hospice</span>
      </h2>
      <p class="body-copy">At Halloway's Funeral Service, we understand the importance of having a working partnership with hospice and open communication with our families during this difficult time. That is why, Halloway's pride themselves in maintaining strong, transparent enduring relationships with a majority of local hospice providers.</p>
    </div>
  </section>

  <section class="spread spread--veterans">
    <div class="panel-frame panel-frame--left"></div>
    <div class="panel-frame panel-frame--right"></div>
    <div class="photo-stack photo-stack--left">
      <div class="deckled back-card--grey"></div>
      <div class="deckled back-card--aged"></div>
      <div class="deckled back-card--pale"></div>
      <div class="deckled front-card"><div class="photo photo--flag" role="img" aria-label="Hands presenting a folded American flag at a memorial service"></div></div>
    </div>
    <div class="panel-copy">
      <h2 class="headline">
        <span class="headline__main">HONORING</span>
        <span class="headline__link">OUR</span>
        <span class="headline__script">Veterans</span>
      </h2>
      <p class="body-copy">Serving our Nation, protecting fellow countrymen, and safe guarding American freedoms, this is the call of duty. We respect a soldier's life and specialize in honoring veterans with a fitting tribute. Halloway's educated staff will aid you in the process of filing for VA benefits owed to your family.</p>
      <p class="body-copy body-copy--closing">Let us provide you with a final salute.</p>
    </div>
  </section>

  <section class="spread spread--facility">
    <div class="panel-frame panel-frame--left"></div>
    <div class="panel-frame panel-frame--right"></div>
    <div class="photo-stack photo-stack--left">
      <div class="deckled back-card--grey"></div>
      <div class="deckled back-card--aged"></div>
      <div class="deckled back-card--pale"></div>
      <div class="deckled front-card"><div class="photo photo--guard" role="img" aria-label="Honor guard soldier in dress uniform holding a ceremonial rifle"></div></div>
    </div>
    <div class="photo-stack photo-stack--right">
      <div class="deckled back-card--grey"></div>
      <div class="deckled back-card--aged"></div>
      <div class="deckled back-card--pale"></div>
      <div class="deckled front-card">
        <div class="photo collage">
          <div class="collage__exterior" role="img" aria-label="Exterior of the funeral home building with entrance drive"></div>
          <div class="collage__foyer" role="img" aria-label="Chandelier-lit foyer with fireplace and seating"></div>
          <div class="collage__lounge" role="img" aria-label="Reception lounge interior"></div>
        </div>
      </div>
    </div>
  </section>

</main>
</body>
</html>
```